ULMIRA card Technical Architecture

Hello everyone ULMIRA: It is a consulting firm in Architecture and Construction. I require a card duplexing, sober, elegant, classic but not boring. Update 1: Use the following data for the card. Name: Gonzalo Pereda Mauricio Villalta Position: COO Twitter: @ulmiraAT Homepage: ulmira-example.com home address not include the participation of all thank you.

Target Market(s)

Construction companies, Architects and Consulting Engineers

Industry/Entity Type

Consulting

Contact Information for Business Card

Los campos que debe tener:
Nombre, Cargo, email, homepage y twitter

Font styles to use
Serif
Sans Serif
Other font styles liked:
• Me gustan playfair display, open sans y roboto, pero estoy sujeto a sus propuestas

Requirements
Must have
• Colors: Present combined proposals in white, red, gray and black Update 1: The two names must be clearly differentiated from the two surnames
Nice to have
• They are free to present their best proposals. I will bring them immediate feedback to the extent you can go see their designs. Complete data for card and logo files will give the winner the

```html
<!DOCTYPE html>
<html lang="en">
<head>
<meta charset="utf-8">
<title>ULMIRA – Business Card</title>
<link rel="stylesheet" href="https://fonts.googleapis.com/css2?family=Open+Sans:wght@400;600;700&family=Arimo:wght@400;700&family=Montserrat:wght@300;400&display=swap">
<style>
  :root {
    --stage: #2b2b2b;
    --card: #000000;
    --band: #9a0000;
    --brand-red: #c8102e;
    --subtitle-red: #b3131b;
    --white: #ffffff;
    --icon-red: #d42a3a;
  }
  * { margin: 0; padding: 0; box-sizing: border-box; }
  html, body {
    width: 1200px;
    height: 900px;
    overflow: hidden;
    background: var(--stage);
  }
  .canvas { position: relative; width: 1200px; height: 900px; }

  .card {
    position: absolute;
    width: 347px;
    height: 560px;
    background: var(--card);
    overflow: hidden;
  }
  .card--front { left: 237px; top: 170px; }
  .card--back  { left: 649px; top: 182px; }

  /* Front */
  .front__brand {
    position: absolute;
    top: 100px; left: 0; width: 100%;
    text-align: center;
    font-family: "Open Sans", sans-serif;
    font-weight: 600;
    font-size: 40px;
    letter-spacing: 6px;
    color: var(--brand-red);
  }
  .front__band {
    position: absolute;
    top: 241px; left: 0;
    width: 100%; height: 223px;
    background: var(--band);
    color: var(--white);
    text-align: center;
  }
  .person__name {
    margin-top: 29px;
    font-family: "Open Sans", sans-serif;
    font-weight: 700;
    font-size: 19px;
  }
  .person__role {
    margin-top: 2px;
    font-family: "Open Sans", sans-serif;
    font-size: 17px;
  }
  .contact {
    list-style: none;
    margin-top: 34px;
    font-family: Arimo, sans-serif;
    font-size: 17px;
    line-height: 23px;
  }
  .contact__label { font-weight: 700; }
  .social {
    position: absolute;
    top: 492px; left: 0; width: 100%;
    display: flex; justify-content: center; align-items: center; gap: 6px;
    font-family: Arimo, sans-serif;
    font-size: 19px;
    color: var(--white);
  }
  .social__mark {
    width: 16px; height: 16px;
    background: var(--icon-red);
    border-radius: 3px;
  }

  /* Back */
  .wordmark {
    position: absolute;
    left: 118px; top: 130px;
    writing-mode: vertical-rl;
    font-family: Montserrat, sans-serif;
    font-weight: 400;
    font-size: 52px;
    letter-spacing: 19px;
    line-height: 1;
    color: var(--white);
  }
  .tagline {
    position: absolute;
    left: 94px; top: 134px;
    height: 300px;
    padding-right: 6px;
    border-right: 1px solid var(--subtitle-red);
    writing-mode: vertical-rl;
    font-family: Montserrat, sans-serif;
    font-weight: 300;
    font-size: 13px;
    letter-spacing: 5.2px;
    line-height: 1;
    color: var(--subtitle-red);
  }
  .back__square {
    position: absolute;
    left: 186px; top: 250px;
    width: 44px; height: 44px;
    background: var(--brand-red);
  }
</style>
</head>
<body>
<main class="canvas">
  <section class="card card--front" aria-label="Card front">
    <div class="front__brand">ULMIRA</div>
    <div class="front__band">
      <p class="person__name">Dario Velmont, BSc.</p>
      <p class="person__role">Owner and Creative Superhero</p>
      <ul class="contact">
        <li><span class="contact__label">P:</span> 00 (0) 555 010 20 30</li>
        <li><span class="contact__label">E:</span> info@ulmira-example.com</li>
        <li><span class="contact__label">W:</span> www.ulmira-example.com</li>
      </ul>
    </div>
    <div class="social"><span class="social__mark" aria-hidden="true"></span>/ulmiraAT</div>
  </section>

  <section class="card card--back" aria-label="Card back">
    <div class="tagline">ARQUITECTURA TÉCNICA</div>
    <div class="wordmark">ULMIRA</div>
    <div class="back__square" aria-hidden="true"></div>
  </section>
</main>
</body>
</html>
```